Cool business cards

Use my existing logo from mark meadow (see images I have uploaded) and design a really cool non-stuffy business card. I am a divorce mediator.

```html
<!DOCTYPE html>
<html lang="en">
<head>
<meta charset="utf-8">
<title>Mark Meadow – Business Card</title>
<link href="https://fonts.googleapis.com/css2?family=Khand:wght@600&family=Roboto:wght@400&display=swap" rel="stylesheet">
<style>
  :root {
    --bg: #ece9e4;
    --teal-light: #45a896;
    --teal-dark: #2a8579;
    --frost: #dcd7cf;
    --frost-edge: #bfb8ae;
    --seam: #8a7d70;
    --ink-light: #eef3ef;
    --ink-address: #d9c9bd;
    --brand-green: #2f8a5a;
    --tag-teal: #2b9a8c;
  }
  * { margin: 0; padding: 0; box-sizing: border-box; }
  html, body { width: 1200px; height: 1054px; overflow: hidden; background: var(--bg); }
  .canvas { position: relative; width: 1200px; height: 1054px; }
  .card {
    position: absolute; left: 100px; top: 224px; width: 1000px; height: 606px;
    box-shadow: 0 14px 40px rgba(0,0,0,.18); overflow: hidden; border-radius: 3px;
  }
  .card-art { position: absolute; inset: 0; }
  .holder { position: absolute; left: 51px; color: var(--ink-light); font-family: "Roboto", sans-serif; }
  .holder-name { top: 86px; font-family: "Khand", sans-serif; font-weight: 600; font-size: 40px; line-height: 1; }
  .holder-role { top: 136px; font-size: 25px; }
  .contact-list { position: absolute; left: 51px; top: 404px; list-style: none; font-family: "Roboto", sans-serif; color: var(--ink-light); font-size: 24px; }
  .contact-list li { display: flex; align-items: center; height: 38px; }
  .contact-icon { width: 22px; height: 22px; margin-right: 25px; fill: var(--ink-light); }
  .address { position: absolute; left: 51px; top: 530px; font-family: "Roboto", sans-serif; font-size: 24px; color: var(--ink-address); }
</style>
</head>
<body>
<div class="canvas">
  <div class="card">
    <svg class="card-art" width="1000" height="606" viewBox="0 0 1000 606">
      <defs>
        <linearGradient id="tealFill" x1="0" y1="0" x2="1" y2="1">
          <stop offset="0" stop-color="var(--teal-light)"/>
          <stop offset="1" stop-color="var(--teal-dark)"/>
        </linearGradient>
        <linearGradient id="frostFill" x1="0" y1="0" x2="0" y2="1">
          <stop offset="0" stop-color="#e4e0da"/>
          <stop offset="1" stop-color="var(--frost)"/>
        </linearGradient>
      </defs>
      <rect class="frost-panel" width="1000" height="606" fill="url(#frostFill)"/>
      <path class="seam" d="M0 0 H660 Q560 303 652 606 H0 Z" fill="var(--seam)"/>
      <path class="teal-panel" d="M0 0 H649 Q551 303 642 606 H0 Z" fill="url(#tealFill)"/>
      <text class="brand-name" transform="translate(773 303) rotate(-90)" text-anchor="middle"
            font-family="Roboto, sans-serif" font-size="46" fill="var(--brand-green)">mark meadow</text>
      <path class="tag-rule" d="M839 64 L842 188 L839 190 L836 188 Z" fill="var(--brand-green)"/>
      <path class="tag-rule" d="M839 500 L842 502 L839 590 L836 502 Z" fill="var(--brand-green)"/>
      <text class="tagline" transform="translate(846 345) rotate(-90)" text-anchor="middle"
            font-family="Roboto, sans-serif" font-size="19" letter-spacing="1" fill="var(--tag-teal)">I AM A DIVORCE MEDIATOR</text>
    </svg>

    <div class="holder holder-name">Dana Whitfield</div>
    <div class="holder holder-role">Managing Director</div>

    <ul class="contact-list">
      <li><svg class="contact-icon" viewBox="0 0 24 24" aria-hidden="true"><path d="M3 9c0-3 4-5 9-5s9 2 9 5v2h-5V9H8v2H3z M6 12h12l2 8H4z"/></svg>828-555-0142</li>
      <li><svg class="contact-icon" viewBox="0 0 24 24" aria-hidden="true"><path d="M2 5h20v14H2z M3 6l9 7 9-7" fill="none" stroke="var(--ink-light)" stroke-width="2"/></svg>dana@markmeadow.com</li>
      <li><svg class="contact-icon" viewBox="0 0 24 24" aria-hidden="true"><g fill="none" stroke="var(--ink-light)" stroke-width="1.8"><circle cx="12" cy="12" r="9"/><ellipse cx="12" cy="12" rx="4" ry="9"/><path d="M3 12h18M5 7h14M5 17h14"/></g></svg>www.markmeadow.com</li>
    </ul>

    <div class="address">58 Willow Lane, Fairbrook, US 28801</div>
  </div>
</div>
</body>
</html>
```